Social media app sign-up flow that asks users to give personal info and connect with other apps

Design an interactive, fun, and playful sign-up flow in which you are providing information about you, your interests, and connecting with different API plug-ins such as Chatterloop, Workvine, Tunevale, etc. (using the brand palette attached).

Basic wireframe, and business requirements are also attached.

Target Market(s)

Gen Z + Millennials (ages 22-40)

Font styles to use
Sans Serif

Colors
fbed22
fbee3d
fbf289

Requirements
Must have
• Forms for users to submit their info. Follow the color palette attached.

Connect with Chatterloop, Connect with Workvine, Connect with Tunevale, Connect with Gatherpost buttons
Nice to have
• I like the way you can use cards to submit your information for each category. Interactive card design for providing your info
Should not have
• Basic outdated designs, long forms

```html
<!DOCTYPE html>
<html lang="en">
<head>
<meta charset="utf-8">
<title>Sign-up Flow Screens</title>
<link href="https://fonts.googleapis.com/css2?family=IBM+Plex+Sans:wght@400;500;600;700&display=swap" rel="stylesheet">
<style>
:root{
  --backdrop:#0c3a4f;
  --screen-light:#ececec;
  --screen-dark:#2a2c31;
  --ink:#222428;
  --ink-soft:#3a3c40;
  --white:#ffffff;
  --field-line:#d4d4d4;
  --yellow:#fcc22f;
  --tan:#cdb272;
  --chatterloop:#3d5a9a;
  --workvine:#1a78c2;
  --workvine-light:#149be0;
  --gatherpost:#e9573a;
  --tunevale:#149be0;
  --tunevale-green:#7ed957;
  --music-bg:#e3e5ee;
  --slate-top:#6b7688;
  --slate-mid:#8a93a2;
  --peach:#f6d7b5;
  --blush:#f8b8a8;
}
*{box-sizing:border-box;margin:0;padding:0}
html,body{width:737px;height:1200px;overflow:hidden}
body{background:var(--backdrop);font-family:"IBM Plex Sans",Arial,sans-serif;position:relative;color:var(--ink)}
.screen{position:absolute;width:228px;height:493px;border-radius:22px;overflow:hidden}
.screen--signup{left:113px;top:82px;background:var(--screen-light)}
.screen--about{left:399px;top:82px;background:var(--screen-dark)}
.screen--places{left:113px;top:634px;background:linear-gradient(180deg,var(--slate-top),var(--slate-mid))}
.screen--music{left:399px;top:634px;background:var(--music-bg)}
.abs{position:absolute}

/* Sign up */
.signup-title{top:28px;width:100%;text-align:center;font-size:21px;font-weight:700}
.field{left:18px;width:192px;background:var(--white);border:1px solid var(--field-line);padding:0 15px;font-size:9px;display:flex;flex-direction:column;justify-content:center}
.field--select{top:73px;height:41px}
.field--select .value{font-weight:500}
.field--select svg{position:absolute;right:9px;top:17px}
.field--phone{top:121px;height:32px}
.note{top:168px;width:100%;text-align:center;font-size:8.5px;line-height:12px;color:var(--ink-soft)}
.login-btn{left:18px;top:203px;width:192px;height:30px;background:var(--ink);color:var(--white);font-weight:700;font-size:12.5px;display:flex;align-items:center;justify-content:center;letter-spacing:.3px}
.divider{top:253px;left:18px;width:192px;display:flex;align-items:center;gap:14px;font-weight:600;font-size:12px}
.divider::before,.divider::after{content:"";flex:1;height:1px;background:#c9c9c9}
.connect{left:18px;width:192px;height:28px;border-radius:14px;color:var(--white);font-size:10.5px;font-weight:600;display:flex;align-items:center;justify-content:center;padding-left:20px}
.connect::before{content:"";position:absolute;left:5px;top:5px;width:18px;height:18px;border-radius:50%;background:rgba(255,255,255,.28)}
.c-chatterloop{background:var(--chatterloop)}
.c-workvine{background:var(--workvine)}
.c-workvine-light{background:var(--workvine-light)}
.c-gatherpost{background:var(--gatherpost)}
.c-tunevale{background:var(--tunevale)}
.c-tunevale-green{background:var(--tunevale-green)}
.account{top:449px;width:100%;text-align:center;font-size:10px}
.account b{font-weight:600}

/* About */
.about-title{top:16px;width:100%;text-align:center;color:var(--white);font-size:14px;font-weight:700;letter-spacing:.3px}
.card{width:95px;height:97px;border-radius:3px;display:flex;flex-direction:column;align-items:center;padding-top:12px;color:var(--white);font-size:10px;font-weight:600;line-height:13px;text-align:center}
.card--yellow{background:var(--yellow)}
.card--tan{background:var(--tan)}
.card .icon{width:40px;height:40px;border-radius:50%;background:var(--white);display:flex;align-items:center;justify-content:center;margin-bottom:9px}
.col-a{left:15px}.col-b{left:118px}
.row-1{top:50px}.row-2{top:160px}.row-3{top:269px}.row-4{top:378px}

/* Shared list screens */
.topbar{top:20px;left:13px;right:13px;display:flex;justify-content:space-between}
.list-title{width:100%;text-align:center;font-size:14px;font-weight:600;letter-spacing:.3px}
.chip{width:95px;height:37px;background:var(--white);border-radius:3px;font-size:9.5px;display:flex;align-items:center;justify-content:space-between;padding:0 10px 0 12px;white-space:nowrap}
.chip .x{font-size:10px;font-weight:700}
.entry{left:15px;width:198px;height:37px;background:var(--white);border-radius:3px;font-size:9.5px;display:flex;align-items:center;padding-left:12px}
.suggest{left:25px;width:177px;height:39px;background:var(--white);border-radius:3px;box-shadow:0 2px 5px rgba(0,0,0,.25);font-size:9.5px;font-weight:500;display:flex;align-items:center;padding-left:13px}

.places-scene{left:0;top:0;width:228px;height:280px;background:linear-gradient(180deg,#6d7789,#8b94a2 60%,#737d8d)}
.places-ground{left:-40px;top:262px;width:308px;height:260px;border-radius:50% 50% 0 0/26px 26px 0 0;background:linear-gradient(180deg,var(--peach),var(--blush))}
.skyline{left:0;top:428px;width:228px;height:65px;background:linear-gradient(180deg,rgba(120,120,140,0) 0%,rgba(110,100,120,.45) 60%,rgba(90,80,100,.6))}
.music-art{left:0;top:393px;width:228px;height:100px;background:linear-gradient(180deg,rgba(227,229,238,0),rgba(236,214,190,.55))}
</style>
</head>
<body>

<section class="screen screen--signup">
  <h1 class="abs signup-title">Sign Up</h1>
  <div class="abs field field--select">
    <span>Country Region</span>
    <span class="value">United States (+1)</span>
    <svg width="7" height="5" viewBox="0 0 7 5"><path d="M.5.5 3.5 3.8 6.5.5" fill="none" stroke="#333" stroke-width="1"/></svg>
  </div>
  <div class="abs field field--phone">Phone Number</div>
  <p class="abs note">We'll call or text you to confirm your number.<br>Standard message and data rates apply.</p>
  <div class="abs login-btn">LOGIN</div>
  <div class="abs divider">or</div>
  <div class="abs connect c-chatterloop" style="top:284px">Continue with Chatterloop</div>
  <div class="abs connect c-workvine" style="top:322px">Connect with Workvine</div>
  <div class="abs connect c-gatherpost" style="top:360px">Connect with Gatherpost</div>
  <div class="abs connect c-tunevale" style="top:399px">Connect with Tunevale</div>
  <p class="abs account">Already have an account? <b>Log in</b></p>
</section>

<section class="screen screen--about">
  <h2 class="abs about-title">TELL ME ABOUT YOU</h2>

  <div class="abs card card--yellow col-a row-1">
    <span class="icon"><svg width="18" height="16" viewBox="0 0 24 21"><path d="M12 21 2 11A6 6 0 0 1 12 3a6 6 0 0 1 10 8z" fill="#222"/></svg></span>
    Places I've<br>Lived
  </div>
  <div class="abs card card--tan col-b row-1">
    <span class="icon"><svg width="18" height="17" viewBox="0 0 24 22"><path d="M12 0 1 6h22zM3 8h3v9H3zm5 0h3v9H8zm5 0h3v9h-3zm5 0h3v9h-3zM1 19h22v3H1z" fill="#222"/></svg></span>
    Schools I've<br>Attended
  </div>
  <div class="abs card card--tan col-a row-2">
    <span class="icon"><svg width="22" height="16" viewBox="0 0 30 22"><circle cx="8" cy="5" r="4" fill="#222"/><circle cx="16" cy="5" r="4" fill="#222"/><path d="M1 18a7 7 0 0 1 14 0zM10 18a7 7 0 0 1 12-4" fill="#222"/><circle cx="23" cy="15" r="5" fill="none" stroke="#222" stroke-width="3"/></svg></span>
    Places I've<br>Worked
  </div>
  <div class="abs card card--yellow col-b row-2">
    <span class="icon"><svg width="15" height="17" viewBox="0 0 20 22"><circle cx="10" cy="6" r="5.5" fill="#222"/><path d="M0 22a10 8 0 0 1 20 0z" fill="#222"/></svg></span>
    People I<br>Know
  </div>
  <div class="abs card card--tan col-a row-3">
    <span class="icon"><svg width="16" height="17" viewBox="0 0 20 22"><rect x="0" y="3" width="20" height="19" rx="2" fill="#222"/><rect x="4" y="0" width="2" height="5" fill="#222"/><rect x="14" y="0" width="2" height="5" fill="#222"/><rect x="2" y="8" width="16" height="1.5" fill="#fff"/><rect x="4" y="12" width="6" height="5" fill="#fff"/></svg></span>
    Events I've<br>Attended
  </div>
  <div class="abs card card--yellow col-b row-3">
    <span class="icon"><svg width="16" height="17" viewBox="0 0 20 22"><rect x="0" y="3" width="20" height="19" rx="2" fill="#222"/><rect x="4" y="0" width="2" height="5" fill="#222"/><rect x="14" y="0" width="2" height="5" fill="#222"/><g fill="#fff"><rect x="3" y="10" width="4" height="3"/><rect x="8" y="10" width="4" height="3"/><rect x="13" y="10" width="4" height="3"/><rect x="3" y="15" width="4" height="3"/><rect x="8" y="15" width="4" height="3"/><rect x="13" y="15" width="4" height="3"/></g></svg></span>
    Events I'm<br>Attending
  </div>
  <div class="abs card card--tan col-a row-4">
    <span class="icon"><svg width="16" height="17" viewBox="0 0 20 22"><path d="M6 3 20 0v15h-2.5V4L8.5 6v12H6z" fill="#222"/><circle cx="4" cy="18" r="4" fill="#222"/><circle cx="16" cy="15" r="4" fill="#222"/></svg></span>
    Music I<br>Love
  </div>
  <div class="abs card card--yellow col-b row-4">
    <span class="icon"><svg width="22" height="15" viewBox="0 0 30 20"><circle cx="15" cy="5" r="4.5" fill="#222"/><circle cx="6" cy="7" r="3.2" fill="#222"/><circle cx="24" cy="7" r="3.2" fill="#222"/><path d="M7 20a8 8 0 0 1 16 0zM0 18a6 6 0 0 1 9-5l-2 5zM30 18a6 6 0 0 0-9-5l2 5z" fill="#222"/></svg></span>
    Teams I<br>Love
  </div>
</section>

<section class="screen screen--places">
  <div class="abs places-scene" role="img" aria-label="Faded city skyline photo behind the form"></div>
  <div class="abs places-ground"></div>
  <div class="abs skyline" role="img" aria-label="City landmark skyline illustration"></div>
  <div class="abs topbar">
    <svg width="13" height="11" viewBox="0 0 13 11"><path d="M0 1h13M0 5.5h13M0 10h13" stroke="#fff" stroke-width="2"/></svg>
    <svg width="12" height="12" viewBox="0 0 12 12"><circle cx="5" cy="5" r="3.8" fill="none" stroke="#fff" stroke-width="1.8"/><path d="M8 8l3.3 3.3" stroke="#fff" stroke-width="1.8"/></svg>
  </div>
  <h2 class="abs list-title" style="top:53px;color:var(--white)">PLACES I'VE LIVED</h2>
  <div class="abs chip" style="left:15px;top:86px">Chicago <span class="x">✕</span></div>
  <div class="abs chip" style="left:118px;top:86px">Madrid <span class="x">✕</span></div>
  <div class="abs chip" style="left:15px;top:135px">Paris <span class="x">✕</span></div>
  <div class="abs chip" style="left:118px;top:135px;padding-left:10px;padding-right:6px">Rio de Janiero <span class="x">✕</span></div>
  <div class="abs entry" style="top:183px">Londo|</div>
  <div class="abs suggest" style="top:215px">London, United Kingdom</div>
  <div class="abs connect c-chatterloop" style="top:330px">Continue with Chatterloop</div>
  <div class="abs connect c-workvine-light" style="top:370px">Continue with Workvine</div>
</section>

<section class="screen screen--music">
  <div class="abs music-art" role="img" aria-label="Colourful line-art decoration at the bottom of the screen"></div>
  <div class="abs topbar">
    <svg width="13" height="11" viewBox="0 0 13 11"><path d="M0 1h13M0 5.5h13M0 10h13" stroke="#333" stroke-width="2"/></svg>
    <svg width="12" height="12" viewBox="0 0 12 12"><circle cx="5" cy="5" r="3.8" fill="none" stroke="#333" stroke-width="1.8"/><path d="M8 8l3.3 3.3" stroke="#333" stroke-width="1.8"/></svg>
  </div>
  <h2 class="abs list-title" style="top:41px;color:var(--ink)">MUSIC I LOVE</h2>
  <div class="abs chip" style="left:15px;top:80px;padding-right:8px">The Larkspurs <span class="x">✕</span></div>
  <div class="abs chip" style="left:118px;top:80px">Delphine <span class="x">✕</span></div>
  <div class="abs chip" style="left:15px;top:129px">Nine Volt <span class="x">✕</span></div>
  <div class="abs chip" style="left:118px;top:129px;padding-right:8px">Otis Marlowe <span class="x">✕</span></div>
  <div class="abs entry" style="top:177px">Brielle Spar|</div>
  <div class="abs suggest" style="top:209px">Brielle Sparks</div>
  <div class="abs connect c-chatterloop" style="top:275px">Continue with Chatterloop</div>
  <div class="abs connect c-tunevale-green" style="top:316px">Continue with Tunevale</div>
</section>

</body>
</html>
```